Northgate Roofing Co.
President
Project: Northgate Roofing Co.
Northgate Roofing Co. - Construction
Creative Brief
Professional
Marcus Ellery
58 Quarry Bend Road Millbrook, NJ 08765
office@northgate-roofing-example.com
I will be using gloss plastice business cards

```html
<!DOCTYPE html>
<html lang="en">
<head>
<meta charset="utf-8">
<title>Northgate Roofing Co. – Stationery</title>
<link href="https://fonts.googleapis.com/css2?family=Open+Sans:wght@400;700&display=swap" rel="stylesheet">
<style>
:root{
  --green:#78b52c;
  --green-light:#a9d25c;
  --green-dark:#4f8a17;
  --ink:#555;
  --muted:#888;
  --paper:#ffffff;
  --line:#dcdcdc;
  --bg:#ffffff;
}
*{margin:0;padding:0;box-sizing:border-box}
html,body{width:1200px;height:348px;overflow:hidden;background:var(--bg)}
body{position:relative;font-family:"Open Sans",Arial,sans-serif;color:var(--ink)}
.piece{position:absolute;background:var(--paper);box-shadow:0 1px 3px rgba(0,0,0,.25)}
.brand{color:var(--green);font-weight:700;white-space:nowrap}
.tiny{font-size:3.4px;line-height:1.5;color:var(--ink)}
.band{position:absolute;left:0;right:0;background:linear-gradient(90deg,var(--green-light),var(--green))}
.web{position:absolute;left:0;right:0;text-align:center;color:var(--muted)}

/* master name */
.master-name{position:absolute;left:12px;top:78px}
.master-name .brand{font-size:11px}
.master-name .tagline{font-size:4.5px;color:#777;margin-top:8px}

/* business cards */
.card{left:12px;width:132px;height:77px}
.card-front{top:139px}
.card-back{top:230px}
.card .brand{position:absolute;left:7px;top:8px;font-size:6px}
.card .band{top:28px;height:12px;left:40px;padding-left:6px;color:#fff;font-size:5px;font-weight:700;line-height:12px}
.card .contact{position:absolute;left:46px;top:44px}
.card .web{bottom:3px;font-size:3px}

/* letterheads */
.letterhead{top:19px;width:223px;height:288px}
.letterhead-one{left:161px}
.letterhead-two{left:401px}
.letterhead .brand{position:absolute;left:12px;top:16px;font-size:8px}
.letterhead .contact{position:absolute;left:118px;top:12px;border-left:1px solid var(--line);padding-left:4px}
.letterhead .band{bottom:16px;height:6px}
.letterhead .web{bottom:6px;font-size:3px}

/* small envelopes */
.envelope{left:638px;width:212px;height:77px}
.envelope-one{top:144px}
.envelope-two{top:230px}
.envelope .brand{position:absolute;left:7px;top:8px;font-size:6px}
.envelope .band{bottom:6px;height:4px}
.envelope .web{bottom:1px;font-size:2.6px}

/* envelope stack */
.envelope-stack{position:absolute;left:893px;top:15px}
</style>
</head>
<body>

<div class="master-name">
  <div class="brand">Northgate Roofing Co.</div>
  <p class="tagline">Roofing Concepts</p>
</div>

<section class="piece card card-front">
  <div class="brand">Northgate Roofing Co.</div>
  <div class="band">Marcus Ellery</div>
  <div class="contact tiny">President<br>T: 609-555-0142<br>58 Quarry Bend Road<br>Millbrook, NJ 08765</div>
  <p class="web">www.northgate-roofing-example.com</p>
</section>

<section class="piece card card-back">
  <div class="brand">Northgate Roofing Co.</div>
  <div class="band">Marcus Ellery</div>
  <div class="contact tiny">President<br>T: 609-555-0142<br>office@northgate-roofing-example.com</div>
  <p class="web">www.northgate-roofing-example.com</p>
</section>

<section class="piece letterhead letterhead-one">
  <div class="brand">Northgate Roofing Co.</div>
  <div class="contact tiny">58 Quarry Bend Road<br>Millbrook, NJ 08765<br>T: 609-555-0142<br>office@northgate-roofing-example.com</div>
  <div class="band"></div>
  <p class="web">www.northgate-roofing-example.com</p>
</section>

<section class="piece letterhead letterhead-two">
  <div class="band"></div>
  <p class="web">www.northgate-roofing-example.com</p>
</section>

<section class="piece envelope envelope-one">
  <div class="brand">Northgate Roofing Co.</div>
  <div class="band"></div>
  <p class="web">www.northgate-roofing-example.com</p>
</section>

<section class="piece envelope envelope-two">
  <div class="brand">Northgate Roofing Co.</div>
  <div class="band"></div>
  <p class="web">www.northgate-roofing-example.com</p>
</section>

<svg class="envelope-stack" width="284" height="292" viewBox="0 0 284 292" aria-label="Envelope set">
  <defs>
    <linearGradient id="greyBack" x1="0" y1="0" x2="0" y2="1">
      <stop offset="0" stop-color="#e4e4e4"/><stop offset="1" stop-color="#9c9c9c"/>
    </linearGradient>
    <linearGradient id="greenFlap" x1="0" y1="0" x2="0" y2="1">
      <stop offset="0" stop-color="#a9d25c"/><stop offset="1" stop-color="#4f8a17"/>
    </linearGradient>
  </defs>
  <g class="envelope-grey">
    <rect x="2" y="2" width="278" height="110" fill="url(#greyBack)"/>
    <polygon points="2,2 280,2 141,70" fill="#f4f4f4" stroke="#cfcfcf" stroke-width=".6"/>
    <text x="141" y="34" text-anchor="middle" font-family="Open Sans, Arial, sans-serif" font-weight="700" font-size="7" fill="#78b52c">Northgate Roofing Co.</text>
  </g>
  <g class="envelope-green">
    <rect x="2" y="52" width="278" height="118" fill="#ffffff" stroke="#d0d0d0" stroke-width=".6"/>
    <polygon points="2,52 280,52 141,134" fill="url(#greenFlap)"/>
    <text x="141" y="90" text-anchor="middle" font-family="Open Sans, Arial, sans-serif" font-weight="700" font-size="7" fill="#ffffff">Northgate Roofing Co.</text>
  </g>
  <g class="envelope-white">
    <rect x="2" y="166" width="278" height="118" fill="#ffffff" stroke="#d0d0d0" stroke-width=".6"/>
    <polyline points="2,166 141,236 280,166" fill="none" stroke="#dedede" stroke-width=".8"/>
    <line x1="2" y1="284" x2="118" y2="222" stroke="#e6e6e6" stroke-width=".8"/>
    <line x1="280" y1="284" x2="164" y2="222" stroke="#e6e6e6" stroke-width=".8"/>
  </g>
</svg>

</body>
</html>
```